Inspirational Quotes Poster Set

Brookloft is a stylish coworking space, which has a design-oriented vintage look from the 60's with an industrial touch (www.brookloft-example.com) Brookloft Quote Poster Set of 16 posters. The poster should be typo oriented and rather simple. Reflecting a bit the clean billboard design from the sixties. Minimal / simple graphical elements

Target Market(s)

Startups and Entrepreneurs

Industry/Entity Type

Startup

Font styles to use
Sans Serif

Colors

Designer to choose colors to be used in the design.

Requirements
Must have
• Posters need to be on and very stylish

```html
<!DOCTYPE html>
<html lang="en">
<head>
<meta charset="utf-8">
<title>Brookloft Quote Poster Set – Never Give Up</title>
<link rel="stylesheet" href="https://fonts.googleapis.com/css2?family=Archivo:wdth,wght@62..125,100..900&display=swap">
<style>
  :root {
    --teal: #14a19a;
    --band: #067a6a;
    --paper: #ffffff;
    --veil: #6e9890;
  }
  html, body {
    margin: 0;
    padding: 0;
    overflow: hidden;
    background: var(--teal);
  }
  .poster {
    display: block;
    width: 801px;
    height: 1200px;
    background: var(--teal);
  }
  .headline {
    font-family: "Archivo", sans-serif;
    font-weight: 600;
    font-size: 232px;
    fill: var(--paper);
    font-stretch: 100%;
  }
  .kicker {
    font-family: "Archivo", sans-serif;
    font-weight: 700;
    font-size: 88px;
    font-stretch: 110%;
  }
  .kicker--light { fill: var(--paper); }
  .kicker--veiled { fill: var(--veil); }
  .accent-band { fill: var(--band); }
  .attribution {
    font-family: "Archivo", sans-serif;
    font-weight: 700;
    font-size: 23px;
    font-stretch: 125%;
    fill: var(--paper);
  }
  .brand-name {
    font-family: "Archivo", sans-serif;
    font-weight: 700;
    font-size: 40px;
    fill: var(--paper);
  }
</style>
</head>
<body>
<svg class="poster" viewBox="0 0 801 1200" width="801" height="1200" xmlns="http://www.w3.org/2000/svg">
  <defs>
    <clipPath id="band-clip">
      <rect x="438" y="833" width="363" height="22"/>
    </clipPath>
  </defs>

  <rect width="801" height="1200" fill="var(--teal)"/>

  <g class="headline-stack">
    <text class="headline" x="-4" y="411" textLength="826" lengthAdjust="spacingAndGlyphs">NEVER</text>
    <text class="headline" x="-4" y="600" textLength="826" lengthAdjust="spacingAndGlyphs">NEVER</text>
    <text class="headline" x="-4" y="788" textLength="826" lengthAdjust="spacingAndGlyphs">NEVER</text>
  </g>

  <g class="kicker-group">
    <text class="kicker kicker--light" x="457" y="867" textLength="325" lengthAdjust="spacingAndGlyphs">give up.</text>
    <rect class="accent-band" x="438" y="833" width="363" height="22"/>
    <text class="kicker kicker--veiled" x="457" y="867" textLength="325" lengthAdjust="spacingAndGlyphs" clip-path="url(#band-clip)">give up.</text>
  </g>

  <g class="attribution-block">
    <text class="attribution" x="71" y="1039" textLength="225" lengthAdjust="spacingAndGlyphs">Walter Greyford,</text>
    <text class="attribution" x="71" y="1067" textLength="220" lengthAdjust="spacingAndGlyphs">Founding Member</text>
  </g>

  <text class="brand-name" x="400" y="1145" text-anchor="middle" textLength="175" lengthAdjust="spacingAndGlyphs">brookloft</text>
</svg>
</body>
</html>
```